Harvest Gateway Fellowship Ministries needs a fresh new web design

We are an up and coming multicultural church that aims to bring people into a life changing encounter with God. We need a fresh and inviting website in order to increase our internet presence and make us easier to connect with.
Here are some of the basic requirements for the site:
• Clearly displayed address, service times, and contact info
• A staff profile page
• An area for a calendar with upcoming events and their details
• Social media buttons
• Group pages for the different ministries (youth, children’s church, men, etc…)
• An area for donations and eCommerce
• A resources page for assorted media (podcasts, sermons, videos, etc.…)
• An area for prayer requests.

```html
<!DOCTYPE html>
<html lang="en">
<head>
<meta charset="utf-8">
<title>Harvest Gateway Fellowship Ministries</title>
<link href="https://fonts.googleapis.com/css2?family=Open+Sans:ital,wght@0,400;0,600;0,700;1,400;1,600&display=swap" rel="stylesheet">
<style>
:root{
  --navy:#0b2f84;
  --gold:#f6b532;
  --ink:#1c1c1c;
  --text:#333;
  --muted:#8a8a8a;
  --panel:#f2f2f2;
  --line:#e3e3e3;
  --footer:#1d1d1d;
  --footer-top:#454545;
  --red:#e01b1b;
  --cal-blue:#2f9bd4;
}
*{margin:0;padding:0;box-sizing:border-box}
html,body{width:1085px;height:1200px;overflow:hidden;background:#fff}
body{position:relative;font-family:"Open Sans",Arial,sans-serif;color:var(--text)}
.abs{position:absolute}

/* header */
.brand{left:162px;top:40px;width:170px;display:flex;align-items:center;gap:8px}
.brand-dot{width:26px;height:26px;border-radius:50%;background:var(--gold);flex:none}
.brand-name{font-size:14px;font-weight:600;line-height:1.2;color:var(--navy)}
.social{top:56px;left:712px;display:flex;gap:16px}
.social span{display:block;width:29px;height:29px;border-radius:4px}
.s-feed{background:#f4a623}.s-bird{background:#5cb8e6}.s-book{background:#2f5aa8}.s-link{background:#3aa3d6}.s-video{background:#e02020}
.tagline{right:163px;top:102px;text-align:right;font-size:12px;line-height:19px;color:#555;font-weight:600}

/* nav */
.nav{left:0;top:166px;width:1085px;height:42px;background:var(--navy)}
.nav ul{list-style:none;position:absolute;left:162px;top:0;display:flex;height:42px}
.nav li{font-size:12px;color:#fff;line-height:42px;padding:0 9px;margin-right:24px}
.nav li.active{background:var(--gold)}

/* hero */
.hero{left:162px;top:229px;width:760px;height:332px;
  background:radial-gradient(ellipse at 62% 35%,#f4c06a 0%,#c77a2a 22%,#5a2f14 48%,#140a05 75%,#050302 100%)}
.hero-text{left:221px;top:300px;color:#fff}
.hero-text h1{font-size:37px;font-weight:400;line-height:40px}
.hero-text h2{font-size:23px;font-weight:400;line-height:30px}
.hero-text p{font-size:13px;line-height:16px;width:300px;margin-top:4px}
.btn-gold{left:220px;top:425px;width:97px;height:40px;background:var(--gold);color:#222;font-size:13px;line-height:40px;text-align:center}
.dots{left:521px;top:529px;display:flex;gap:7px}
.dots span{width:10px;height:10px;border-radius:50%;background:var(--gold)}
.dots span:first-child{background:#fff}

/* welcome */
.h-sec{font-size:20px;font-weight:400;color:#222}
.welcome-h{left:162px;top:599px}
.welcome-p{left:162px;top:638px;width:450px;font-size:10.5px;line-height:14px;color:var(--muted)}
.btn-dark{background:linear-gradient(#2a2a2a,#050505);color:#fff;font-size:11px;font-weight:600;text-align:center;border-radius:3px}
.welcome-btn{left:162px;top:703px;width:69px;height:35px;line-height:35px}

/* service times */
.service{left:162px;top:760px;width:194px;height:145px;background:var(--panel);padding:18px 18px}
.service h3{font-size:13px;font-weight:600;color:#111;margin-bottom:8px}
.service table{font-size:11px;color:#333;border-collapse:collapse}
.service td{padding:2px 0;line-height:13px}
.service td:first-child{width:80px;padding-left:2px}
.service a{display:block;margin-top:10px;font-size:11px;color:var(--red);text-decoration:underline}

/* staff */
.staff-h{left:385px;top:761px}
.arrows{left:619px;top:768px;font-size:16px;color:#999;letter-spacing:14px}
.staff-photo{left:385px;top:802px;width:84px;height:84px;border-radius:50%;background:radial-gradient(circle at 50% 40%,#6a5a50,#1b1b1f 60%,#c9d3e0 61%)}
.staff-name{left:493px;top:795px;font-size:13px;line-height:14px;color:#111}
.staff-p{left:493px;top:838px;width:170px;font-size:10px;line-height:14px;color:var(--muted)}
.staff-more{left:493px;top:891px;font-size:10.5px;color:#111;font-weight:600}

/* donate */
.donate{left:162px;top:922px;width:493px;height:150px;background:var(--panel)}
.donate-h{left:18px;top:11px}
.donate-p{left:19px;top:48px;width:450px;font-size:10.5px;line-height:14px;color:var(--muted)}
.donate-btn{left:19px;top:100px;width:68px;height:34px;line-height:34px;font-weight:400}
.pay-btn{left:114px;top:98px;width:71px;height:20px;border-radius:10px;background:linear-gradient(#ffe7a6,#f5b939);font-size:11px;font-weight:700;color:#1a3a7a;text-align:center;line-height:20px}
.cards{left:93px;top:121px;display:flex;gap:3px}
.cards span{width:19px;height:12px;border-radius:1px;background:#c9ccd4}
.cards span:nth-child(odd){background:#9fa7b8}

/* prayer */
.prayer{left:686px;top:585px;width:236px;height:320px;background:#f4f4f4}
.prayer-h{left:17px;top:11px}
.field{left:17px;width:203px;background:#fff;border:1px solid var(--line);font-size:10.5px;color:#aaa;padding:13px 13px}
.f1{top:52px;height:40px}.f2{top:99px;height:40px;padding-top:14px}.f3{top:148px;height:111px;padding-top:10px}
.send{left:18px;top:274px;width:62px;height:33px;line-height:33px;background:#111;color:#fff;font-size:11.5px;text-align:center}

/* calendar */
.cal{left:703px;top:922px;width:187px;height:170px;background:#f3f3f3;border-radius:4px;box-shadow:0 2px 4px rgba(0,0,0,.35);overflow:hidden}
.cal-head{height:31px;background:linear-gradient(#4a4a4a,#2c2c2c);color:#fff;font-size:12px;font-weight:700;text-align:center;line-height:31px;position:relative}
.cal-nav{position:absolute;top:7px;width:18px;height:17px;border-radius:3px;background:#1e1e1e;border:1px solid #555}
.cal-nav.prev{left:6px}.cal-nav.next{right:6px}
.cal-nav::after{content:"";position:absolute;top:5px;border:3px solid transparent}
.cal-nav.prev::after{left:4px;border-right:4px solid #ddd}
.cal-nav.next::after{left:7px;border-left:4px solid #ddd}
.cal-grid{display:grid;grid-template-columns:repeat(7,1fr);gap:1px;padding:8px 3px 0;font-size:11px;text-align:center}
.cal-grid .dow{font-weight:600;color:#222;line-height:18px}
.cal-grid span{line-height:20px;background:#e9e9e9;color:#333}
.cal-grid .o{color:#999}
.cal-grid .today{background:var(--cal-blue);color:#fff}
.ring{top:912px;width:4px;height:20px;border-radius:2px;background:#bbb}
.popup{left:716px;top:1075px;width:162px;height:96px;background:#f0f0f0;border-bottom:2px solid var(--gold);box-shadow:0 1px 4px rgba(0,0,0,.3);padding:7px 12px}
.popup h4{font-size:12.5px;font-style:italic;font-weight:600;color:#222;text-align:center;margin-bottom:5px}
.popup p{font-size:9.5px;font-style:italic;color:#666;line-height:21px;display:flex;align-items:center;gap:7px}
.popup svg{width:10px;height:10px;fill:#777}

/* footer */
.footer{left:0;top:1110px;width:1085px;height:90px;background:var(--footer);border-top:5px solid var(--footer-top)}
.footer ul{list-style:none;position:absolute;left:162px;top:16px;display:flex;gap:42px;font-size:11.5px;color:#fff}
.footer p{position:absolute;left:162px;top:39px;font-size:11.5px;color:#fff}
</style>
</head>
<body>

<header>
  <div class="abs brand"><span class="brand-dot"></span><span class="brand-name">Harvest Gateway Fellowship Ministries</span></div>
  <div class="abs social" aria-label="Social links">
    <span class="s-feed" role="img" aria-label="News feed"></span>
    <span class="s-bird" role="img" aria-label="Short posts"></span>
    <span class="s-book" role="img" aria-label="Community page"></span>
    <span class="s-link" role="img" aria-label="Professional profile"></span>
    <span class="s-video" role="img" aria-label="Video channel"></span>
  </div>
  <div class="abs tagline">Sed ut perspiciatis unde omnis iste natus error sit voluptatem<br>555.013.4820 &nbsp;&nbsp;|&nbsp;&nbsp; info@harvestgateway.org</div>
</header>

<nav class="abs nav">
  <ul>
    <li class="active">Home</li><li>About Us</li><li>Events</li><li>Prayer Request</li><li>Donate</li><li>Contact Us</li>
  </ul>
</nav>

<section class="abs hero" role="img" aria-label="Photograph of a cross on a hill against a glowing sunset sky"></section>
<div class="abs hero-text">
  <h1>HGFM</h1>
  <h2>is located in Queens</h2>
  <p>New York and we would love to have you worship with us.</p>
</div>
<div class="abs btn-gold">Donate Now</div>
<div class="abs dots"><span></span><span></span><span></span></div>

<h2 class="abs h-sec welcome-h">Welcome to HGFM</h2>
<p class="abs welcome-p">Welcome to Harvest Gateway Fellowship Ministries, a place where we can come together and fellowship. HGFM is located in Queens, New York and we would love to have you worship with us.</p>
<div class="abs btn-dark welcome-btn">Read more</div>

<section class="abs service">
  <h3>Service Times</h3>
  <table>
    <tr><td>Mon - Fri</td><td>8 am &nbsp;to &nbsp;6 Pm</td></tr>
    <tr><td>Sat</td><td>8 am &nbsp;to &nbsp;1 Pm</td></tr>
    <tr><td>Sun</td><td>6 am &nbsp;to &nbsp;1 Pm</td></tr>
  </table>
  <a>Choose Your Loaction</a>
</section>

<h2 class="abs h-sec staff-h">Our Staff</h2>
<div class="abs arrows">&#8249;&#8250;</div>
<div class="abs staff-photo" role="img" aria-label="Portrait photo of the pastor"></div>
<div class="abs staff-name">Marcus Ellison-Pastor<br>and Founder</div>
<p class="abs staff-p">Marcus Ellison is a native of the Caribbean island of Jamaica and strongly believes that God’s calling</p>
<div class="abs staff-more">Read More</div>

<section class="abs donate">
  <h2 class="abs h-sec donate-h">Donate</h2>
  <p class="abs donate-p">Making a gift to Harvest Gateway Fellowship Ministries will support us with our community outreach events such as our annual "Back to School" event and our Thanksgiving basket</p>
  <div class="abs btn-dark donate-btn">Read More</div>
  <div class="abs pay-btn">Donate</div>
  <div class="abs cards" aria-label="Accepted payment cards"><span></span><span></span><span></span><span></span><span></span><span></span></div>
</section>

<section class="abs prayer">
  <h2 class="abs h-sec prayer-h">Prayer Request</h2>
  <div class="abs field f1">Enter Your name</div>
  <div class="abs field f2">Enter Your Mail Id</div>
  <div class="abs field f3">Enter Your Message</div>
  <div class="abs send">Send</div>
</section>

<section class="abs cal">
  <div class="cal-head"><span class="cal-nav prev"></span>July 2014<span class="cal-nav next"></span></div>
  <div class="cal-grid">
    <b class="dow">Su</b><b class="dow">Mo</b><b class="dow">Tu</b><b class="dow">We</b><b class="dow">Th</b><b class="dow">Fr</b><b class="dow">Sa</b>
    <span class="o">27</span><span class="o">28</span><span class="o">29</span><span class="o">30</span><span>1</span><span>2</span><span>3</span>
    <span>4</span><span>5</span><span>6</span><span>7</span><span class="today">8</span><span>9</span><span>10</span>
    <span>11</span><span>12</span><span>13</span><span>14</span><span>15</span><span>16</span><span>17</span>
    <span>18</span><span>19</span><span>20</span><span>21</span><span>22</span><span>23</span><span>24</span>
    <span>25</span><span>26</span><span>27</span><span>28</span><span>29</span><span>30</span><span>31</span>
  </div>
</section>
<div class="abs ring" style="left:741px"></div>
<div class="abs ring" style="left:850px"></div>

<div class="abs popup">
  <h4>Meeting with Marcus</h4>
  <p><svg viewBox="0 0 10 10"><path d="M5 0a3.5 3.5 0 0 0-3.5 3.5C1.5 6 5 10 5 10s3.5-4 3.5-6.5A3.5 3.5 0 0 0 5 0zm0 5a1.5 1.5 0 1 1 0-3 1.5 1.5 0 0 1 0 3z"/></svg>Lorem ipsum dolor 12</p>
  <p><svg viewBox="0 0 10 10"><path d="M5 0a5 5 0 1 0 0 10A5 5 0 0 0 5 0zm0 8.8A3.8 3.8 0 1 1 5 1.2a3.8 3.8 0 0 1 0 7.6zM5.5 2.5h-1V5.4l2.2 1.4.5-.8-1.7-1.1z"/></svg>3:50 PM</p>
  <p><svg viewBox="0 0 10 10"><path d="M1 0h1v10H1zM2.5 1h6L7 3.5 8.5 6h-6z"/></svg>Location: Newyork</p>
</div>

<footer class="abs footer">
  <ul><li>Home</li><li>About Us</li><li>Events</li><li>Prayer Request</li><li>Donate</li><li>Contact Us</li></ul>
  <p>Copyright © 2014 harvestgateway.org. All rights reserved</p>
</footer>

</body>
</html>
```